Electrician Business Card/ company logo/small business

New Business Cards and logo needed that will catch peoples eye and say we went that extra step. Attached is a design possibly to be incorporated, if u have your own great, lets see it!... This will be a small local business. thank you for all you do!
Halvern Electric
Ned Fosky Owner
Journeyman Electrician
phone 1.555.208.3471
email: KQLHalvernElectric@quellmail.net
call for free estimate!
Updates

Accepted and approved for cards

Target Market(s)

support small local business

Industry/Entity Type

Electrical,

Contact Information for Business Card

name, title,company/ logo, phone, email, free estimate

Other font styles liked:
• easy to read

Colors

Designer to choose colors to be used in the design.

Requirements
Must have
• eye catching everything! logo and halvern electric listed on business card/logo, incorp logo in the background of card
Nice to have
• lightening bolts in eyes or around the triangle? vertical, modern, any design that would be unique and stand out
Should not have
• pinks, reds, yellows,brown

```html
<!DOCTYPE html>
<html lang="en">
<head>
<meta charset="utf-8">
<title>Halvern Electric – Business Card</title>
<link rel="stylesheet" href="https://fonts.googleapis.com/css2?family=Michroma&family=Mulish:wght@600;700;800&display=swap">
<style>
  :root{
    --stage:#e4e4e7;
    --card:#232323;
    --card-light:#2d2f2f;
    --lime:#a6c21b;
    --cyan:#14aee0;
    --blue:#0f88cf;
    --white:#ffffff;
  }
  *{margin:0;padding:0;box-sizing:border-box}
  html,body{width:1200px;height:1200px;overflow:hidden}
  body{background:var(--stage);font-family:"Mulish",sans-serif;position:relative}
  .card{position:absolute;top:190px;width:460px;height:820px;background:var(--card);overflow:hidden}
  .card--front{left:100px}
  .card--back{left:640px;display:flex;align-items:center;justify-content:center}
  .card__facets{position:absolute;inset:0;width:100%;height:100%}
  .brand{position:absolute;display:flex;align-items:center;gap:14px}
  .card--front .brand{left:42px;top:150px}
  .card--back .brand{position:static}
  .brand__square{width:22px;height:22px;background:var(--lime)}
  .brand__name{font-family:"Michroma",sans-serif;font-size:26px;color:var(--lime);letter-spacing:1px;line-height:1.2}
  .person{position:absolute;left:42px;top:402px}
  .person__name{font-family:"Michroma",sans-serif;font-size:34px;color:var(--cyan);letter-spacing:2px;line-height:1}
  .person__role{margin-top:14px;font-size:24px;font-weight:700;color:var(--white);letter-spacing:2px}
  .divider{position:absolute;left:42px;right:0;top:493px;height:4px;background:linear-gradient(90deg,var(--lime),var(--blue))}
  .trade{position:absolute;left:42px;top:514px;font-size:24px;font-weight:600;color:var(--lime);letter-spacing:.3px}
  .contact{position:absolute;left:42px;top:630px;list-style:none}
  .contact__item{display:flex;align-items:center;gap:12px;color:var(--white);font-weight:700}
  .contact__item + .contact__item{margin-top:26px}
  .contact__icon{width:41px;height:39px;background:linear-gradient(135deg,var(--lime),var(--blue));display:flex;align-items:center;justify-content:center;flex:none}
  .contact__phone{font-size:30px;letter-spacing:1px}
  .contact__email{font-size:16.5px}
</style>
</head>
<body>

<section class="card card--front">
  <svg class="card__facets" viewBox="0 0 460 820" preserveAspectRatio="none" aria-hidden="true">
    <polygon points="0,12 150,70 0,125" fill="#262626"/>
    <polygon points="0,125 150,70 260,20 460,20 460,105 330,170 150,245 0,300" fill="#2a2a2a"/>
    <polygon points="0,300 150,245 330,170 460,105 460,210 300,290 145,250" fill="#2e302f"/>
    <polygon points="145,250 300,290 460,210 460,295 380,330" fill="#292929"/>
    <polygon points="380,330 460,295 460,385" fill="#2c2e2e"/>
    <polygon points="0,190 150,245 0,300" fill="#303232"/>
  </svg>

  <div class="brand">
    <span class="brand__square"></span>
    <span class="brand__name">HALVERN Electric</span>
  </div>

  <div class="person">
    <h1 class="person__name">NED FOSKY</h1>
    <p class="person__role">OWNER</p>
  </div>
  <div class="divider"></div>
  <p class="trade">JOURNEYMAN ELECTRICIAN</p>

  <ul class="contact">
    <li class="contact__item">
      <span class="contact__icon">
        <svg width="22" height="22" viewBox="0 0 24 24" fill="none" stroke="#fff" stroke-width="1.4" stroke-linejoin="round"><path d="M5 3l4 1 1 5-2 1.5a11 11 0 0 0 5.5 5.5L15 14l5 1 1 4-2 2C10 21 3 14 3 5z"/></svg>
      </span>
      <span class="contact__phone">1.555.208.3471</span>
    </li>
    <li class="contact__item">
      <span class="contact__icon">
        <svg width="24" height="18" viewBox="0 0 24 18" fill="none" stroke="#fff" stroke-width="1.4"><rect x="1" y="2" width="22" height="14"/><path d="M1 2l11 8 11-8M1 16l8-7M23 16l-8-7"/></svg>
      </span>
      <span class="contact__email">KQLHalvernElectric@quellmail.net</span>
    </li>
  </ul>
</section>

<section class="card card--back">
  <div class="brand">
    <span class="brand__square"></span>
    <span class="brand__name">HALVERN Electric</span>
  </div>
</section>

</body>
</html>
```